korval Business Cards

We need a business card design for korval (Logo Attached), a management consultancy specialized in brand & business building.

Design should be clean, smart and a touch of innnovation without being gimmicky.

The details on the card should be:
Name: Tomas Velduren
Title: Managing Director
Address: 42 Marlowe Pier, Tarn Vessel Tower, Singapore 073926
Tel: +6285927461082
email: tv@korvaladvise.example
website: korvaladvise.example

For further background on corporate identity, please check www.korvaladvise.example
Updates

Dear all,

Many thanks for the submissions so far! I gave feedback to those designs that I prefer at this stage.

Overall I see that my preference goes into the direction that 'less is more' and 'simple is beautiful'

Please create uniqueness and standout by the simplicity and attraction of the overall concept and design.

Many thanks and please shout incase of questions!

Tomas

Industry/Entity Type

Business

```html
<!DOCTYPE html>
<html lang="en">
<head>
<meta charset="utf-8">
<title>Korval Business Cards</title>
<link rel="stylesheet" href="https://fonts.googleapis.com/css2?family=Open+Sans:wght@400;600;700&display=swap">
<style>
  :root {
    --backdrop: #e9e7e3;
    --card: #ffffff;
    --ink: #4a4a4c;
    --accent: #f26b12;
    --band: #4b4b4d;
    --rule: #9a9a9a;
  }
  * { margin: 0; padding: 0; box-sizing: border-box; }
  html, body {
    width: 1174px; height: 1200px; overflow: hidden;
    background: var(--backdrop);
    font-family: "Open Sans", Arial, sans-serif;
    color: var(--ink);
  }
  .sheet { position: relative; width: 1174px; height: 1200px; }
  .card {
    position: absolute; width: 944px; height: 538px;
    background: var(--card);
    border: 1px solid #2f2f2f;
    overflow: hidden;
  }
  .card--front { left: 29px; top: 39px; }
  .card--back { left: 186px; top: 618px; }

  .wordmark {
    position: absolute; left: 0; right: 0;
    text-align: center;
    font-weight: 600; font-size: 84px; letter-spacing: 2px;
    color: var(--ink); line-height: 1;
  }
  .card--front .wordmark { top: 68px; }
  .card--back .wordmark { top: 228px; }

  .identity {
    position: absolute; right: 439px; top: 253px;
    text-align: right; font-size: 22px; line-height: 33px;
  }
  .identity__name { font-weight: 700; font-size: 27px; line-height: 34px; }
  .identity__title { color: var(--accent); margin-bottom: 4px; }

  .divider {
    position: absolute; left: 520px; top: 254px;
    width: 1px; height: 140px; background: var(--rule);
  }
  .contacts {
    position: absolute; left: 530px; top: 247px;
    list-style: none; font-size: 22px;
  }
  .contacts li {
    display: flex; align-items: center; gap: 10px;
    height: 48px;
  }
  .contacts svg { width: 19px; height: 19px; flex: none; }

  .wave { position: absolute; left: 0; bottom: 0; width: 944px; height: 538px; }

  .site {
    position: absolute; left: 0; right: 0; top: 400px;
    text-align: center; font-size: 24px; letter-spacing: 4px;
    color: var(--ink);
  }
</style>
</head>
<body>
<main class="sheet">
  <section class="card card--front">
    <div class="wordmark">korval</div>

    <div class="identity">
      <div class="identity__name">Tomas Velduren</div>
      <div class="identity__title">Managing Director</div>
      <div class="identity__address">42 Marlowe Pier, Tarn<br>Vessel Tower, Singapore 073926</div>
    </div>

    <div class="divider"></div>

    <ul class="contacts">
      <li>
        <svg viewBox="0 0 20 20" aria-hidden="true"><circle cx="10" cy="10" r="8.5" fill="none" stroke="var(--accent)" stroke-width="1.6"/><path d="M7 5.5c-1 1-1 3 1 5.5s4.5 3.5 5.5 2.5l-1.5-2-1.5.8c-1-.5-2.2-1.8-2.6-2.8l.9-1.4z" fill="var(--accent)"/></svg>
        <span>+6285927461082</span>
      </li>
      <li>
        <svg viewBox="0 0 20 20" aria-hidden="true"><rect x="1.5" y="4" width="17" height="12" rx="1.5" fill="var(--accent)"/><path d="M2.5 5l7.5 6 7.5-6" fill="none" stroke="#fff" stroke-width="1.6"/></svg>
        <span>tv@korvaladvise.example</span>
      </li>
      <li>
        <svg viewBox="0 0 20 20" aria-hidden="true"><circle cx="10" cy="10" r="8.5" fill="var(--accent)"/><g fill="none" stroke="#fff" stroke-width="1.1"><ellipse cx="10" cy="10" rx="3.5" ry="8.5"/><path d="M1.5 10h17M3 5.8h14M3 14.2h14"/></g></svg>
        <span>www.korvaladvise.example</span>
      </li>
    </ul>

    <svg class="wave" viewBox="0 0 944 538" aria-hidden="true">
      <path d="M0 472 C240 525 600 468 944 532 L944 538 L0 538 Z" fill="var(--band)"/>
      <path d="M0 412 C50 452 190 486 400 482 C610 478 800 494 944 520 L944 526 C800 504 610 488 400 494 C190 500 40 486 0 468 Z" fill="var(--accent)"/>
    </svg>
  </section>

  <section class="card card--back">
    <div class="wordmark">korval</div>
    <div class="site">www.korvaladvise.example</div>
  </section>
</main>
</body>
</html>
```